Brightfield Ventures Inc. Letterhead

Creation of attractive and eye catching letterhead for a business start-up for the construction industry. Letterhead must relate to construction, but avoid standard hammer and tools in the design.

I forgot to add some details, sorry about that. Some pertinent info: Ph: 916-555-0187 brightfieldventures.example 448 Willowmere Ave, Ste 210 Folsom, CA 95999 info@brightfieldventures.example not sure if slogan should be in there" “Connecting construction professionals to create a purpose driven industry.” must be able to be used in word. Thanks!

```html
<!DOCTYPE html>
<html lang="en">
<head>
<meta charset="utf-8">
<title>Brightfield Ventures Inc. Letterhead</title>
<link href="https://fonts.googleapis.com/css2?family=Lato:wght@400;700&family=Kaushan+Script&display=swap" rel="stylesheet">
<style>
  :root {
    --navy: #1b1e58;
    --red: #c1202a;
    --ink: #4a4a4f;
    --rule: #c9c9cf;
    --paper: #ffffff;
  }
  * { margin: 0; padding: 0; box-sizing: border-box; }
  html, body {
    width: 897px; height: 1200px; overflow: hidden;
    background: var(--paper);
  }
  .letterhead {
    position: relative;
    width: 897px; height: 1200px;
    background: var(--paper);
    font-family: "Lato", sans-serif;
    color: var(--ink);
  }
  .brand {
    position: absolute; left: 74px; top: 62px;
    display: flex; align-items: center; gap: 12px;
  }
  .brand-mark {
    width: 18px; height: 18px; background: var(--red); flex: none;
  }
  .brand-name {
    font-weight: 700; font-size: 23px; letter-spacing: 2.5px;
    color: var(--navy); text-transform: uppercase; line-height: 30px;
  }
  .contact {
    position: absolute; left: 627px; top: 44px;
    border-left: 1px solid var(--rule);
    padding-left: 12px;
    font-style: normal;
    font-size: 13px; line-height: 20px; color: #444;
  }
  .contact-row { display: flex; gap: 5px; align-items: flex-start; }
  .contact-row.gap { margin-top: 12px; }
  .contact-row svg { width: 10px; height: 10px; margin-top: 5px; flex: none; fill: var(--red); }
  .letter {
    position: absolute; left: 77px; top: 320px; width: 743px;
  }
  .salutation {
    font-weight: 700; font-size: 17px; color: var(--navy);
    margin-bottom: 20px;
  }
  .letter p {
    font-size: 17.4px; line-height: 27.6px;
    text-align: justify; hyphens: manual;
    margin-bottom: 21px;
  }
  .closing { margin-top: 32px; font-size: 19.5px; color: #222; }
  .signature {
    font-family: "Kaushan Script", cursive;
    font-size: 32px; color: var(--navy); margin-top: 6px;
  }
  .footer-band {
    position: absolute; left: 0; bottom: 0; width: 897px; height: 44px;
  }
  .footer-url {
    position: absolute; right: 40px; bottom: 11px;
    color: #fff; font-size: 16px; letter-spacing: 1px;
  }
  .footer-url strong { font-weight: 700; }
</style>
</head>
<body>
<main class="letterhead">
  <header>
    <div class="brand">
      <span class="brand-mark"></span>
      <span class="brand-name">Brightfield<br>Ventures</span>
    </div>
    <address class="contact">
      <div class="contact-row">
        <svg viewBox="0 0 10 10"><path d="M5 0a3.5 3.5 0 0 0-3.5 3.5C1.5 6 5 10 5 10s3.5-4 3.5-6.5A3.5 3.5 0 0 0 5 0zm0 5a1.5 1.5 0 1 1 0-3 1.5 1.5 0 0 1 0 3z"/></svg>
        <span>448 Willowmere Ave, Ste 210<br>Folsom, CA 95999</span>
      </div>
      <div class="contact-row gap">
        <svg viewBox="0 0 10 10"><path d="M2 0.5l2 2-1 1.2c.6 1.3 1.6 2.3 2.9 2.9L7 5.6l2 2-1.2 1.7C4.3 9.5.5 5.7.7 1.9z"/></svg>
        <span>916-555-0187</span>
      </div>
      <div class="contact-row">
        <svg viewBox="0 0 10 10"><path d="M0 2h10v6H0zM0.8 2.6L5 5.6l4.2-3" stroke="#fff" stroke-width="0.8"/></svg>
        <span>info@brightfieldventures.example</span>
      </div>
    </address>
  </header>

  <section class="letter">
    <div class="salutation">Dear Mr. Lorem,</div>
    <p>Lorem ipsum dolor sit amet, consectetuer adipiscing elit, sed diam nonummy nibh euismod tinci&shy;dunt ut laoreet dolore magna aliquam erat volutpat. Ut wisi enim ad minim veniam, quis nostrud exerci tation ullamcorper suscipit lobortis nisl ut aliquip ex ea commodo consequat. Duis autem vel eum iriure dolor in hendiusto odio dignissim qui blandit praesent luptatum zzril delenit augue duis dolore te feugait nulla facilisi.</p>
    <p>Lorem ipsum dolor sit amet, consectetuer adipiscing elit, sed diam nonummy nibh euismod tinci&shy;dunt ut laoreet dolore magna aliquam erat volutpat. Ut wisi enim ad minim veniam, quis nostrud exerci tation ullamcorper suscipit lobortis nisl ut aliquip ex ea commodo consequat. Duis autem vel eum iriure dolor in hendiusto odio dignissim qui blandit praesent luptatum zzril delenit augue duis dolore te feugait nulla facilisi.</p>
    <p>Lorem ipsum dolor sit amet, consectetuer adipiscing elit, sed diam nonummy nibh euismod tinci&shy;dunt ut laoreet dolore magna aliquam erat volutpat. Ut wisi enim ad minim veniam, quis nostrud exerci tation ullamcorper suscipit lobortis nisl ut aliquip ex ea commodo consequat. Duis autem vel eum iriure dolor in hendiusto odio dignissim qui blandit praesent luptatum zzril delenit augue duis dolore te feugait nulla facilisi.</p>
    <div class="closing">Sincerely Your,</div>
    <div class="signature">Your Name</div>
  </section>

  <footer>
    <svg class="footer-band" viewBox="0 0 897 44" preserveAspectRatio="none">
      <polygon points="0,22 560,24 544,44 0,44" fill="var(--red)"/>
      <polygon points="566,44 582,24 560,24 544,44" fill="#fff"/>
      <polygon points="606,2 897,2 897,44 570,44" fill="var(--navy)"/>
    </svg>
    <div class="footer-url">www.<strong>brightfieldventures</strong>.example</div>
  </footer>
</main>
</body>
</html>
```